A5, portrait
Theme is science
audience is VIPS, politicians, executives
this is a really important event, we want a very classy invitation
include logo for bloom and grow and lantern but lantern one bigger
images attached
Have attached some styles we like but doesn't need to be these colours. If we can incorporate some colours from our logo would be good but don't make too colourful and childish

You’re invited to the official opening and launch of Lantern, Centre of Discovery. an industry first, pioneering, STEM hub.

Saturday 30th April, 2022

10:00 am – 12:00 pm

42 Harlow Lane, Fernwood

Light canapes provided. Dress code is smart/casual

All guests will be given a guided walk through of Australia’s first dedicated STEM education hub for children aged 3-6.

Invitation only

RSVP: 18 April to marketing@bloomandgrow.edu.au

```html
<!DOCTYPE html>
<html lang="en">
<head>
<meta charset="utf-8">
<title>Lantern, Centre of Discovery – Official Opening Invitation</title>
<link href="https://fonts.googleapis.com/css2?family=Tinos:wght@400;700&display=swap" rel="stylesheet">
<style>
  :root {
    --backdrop: #221f1a;
    --slate: #4b4a5c;
    --slate-deep: #34334a;
    --indigo: #2a2a5c;
    --violet: #6a64c8;
    --lavender: #a79ae0;
    --ink-light: #f1f0f6;
    --ink-dark: #2b2b33;
    --strip: #f2f2f2;
    --badge-blue: #1f5fb8;
    --accent-gold: #f2c531;
  }
  * { box-sizing: border-box; margin: 0; padding: 0; }
  html, body { width: 1200px; height: 925px; overflow: hidden; }
  body {
    background: var(--backdrop);
    font-family: "Tinos", "Times New Roman", serif;
    color: var(--ink-light);
  }
  .invitation {
    position: absolute;
    left: 310px; top: 52px;
    width: 580px; height: 820px;
    background: radial-gradient(ellipse at 45% 35%, var(--slate) 0%, var(--slate-deep) 70%, var(--indigo) 100%);
    overflow: hidden;
    box-shadow: 0 20px 50px rgba(0,0,0,.5);
  }
  .pattern-band {
    position: absolute; left: 0; width: 100%;
    background: linear-gradient(90deg, #55546a, #5d5c72 50%, #4f4e66);
  }
  .pattern-band--top { top: 0; height: 110px; }
  .pattern-band--bottom { top: 700px; height: 70px; }
  .brand-lantern {
    position: absolute; top: 138px; left: 120px;
    display: flex; align-items: center; gap: 12px;
  }
  .brand-lantern__dot {
    width: 40px; height: 40px; border-radius: 50%;
    background: var(--accent-gold);
  }
  .brand-lantern__name {
    font-size: 38px; font-weight: 700; color: var(--ink-light); letter-spacing: .5px;
  }
  .intro, .details {
    position: absolute; left: 0; width: 100%;
    text-align: center; font-size: 20px; line-height: 1.35;
  }
  .intro { top: 250px; }
  .details { top: 368px; }
  .feature-photo {
    position: absolute; top: 470px; left: 0; width: 100%; height: 230px;
    background: linear-gradient(120deg, #5a56c4 0%, #8c80da 35%, #b6a9e6 55%, #4a3f9a 80%, #2a2660 100%);
  }
  .notes {
    position: absolute; top: 612px; left: 40px; right: 40px;
    text-align: center; font-size: 11.5px; line-height: 1.35;
  }
  .invite-only {
    display: inline-block; margin-top: 10px;
    border: 1.5px solid var(--ink-light); padding: 3px 10px;
    font-size: 13px; letter-spacing: .5px;
  }
  .brand-bloom {
    position: absolute; top: 722px; right: 22px;
    display: flex; align-items: center; gap: 8px;
  }
  .brand-bloom__square { width: 26px; height: 26px; background: var(--badge-blue); }
  .brand-bloom__name { font-size: 14px; color: var(--ink-light); }
  .rsvp {
    position: absolute; top: 770px; left: 0; width: 100%; height: 50px;
    background: var(--strip); color: var(--ink-dark);
    display: flex; align-items: center; justify-content: center;
    font-size: 18px;
  }
</style>
</head>
<body>
  <article class="invitation">
    <div class="pattern-band pattern-band--top" role="img" aria-label="Subtle tonal triangle pattern"></div>

    <div class="brand-lantern">
      <span class="brand-lantern__dot"></span>
      <span class="brand-lantern__name">Lantern</span>
    </div>

    <p class="intro">You’re invited to the official opening and<br>launch of Lantern, Centre of Discovery.<br>An industry first, pioneering, STEM hub.</p>

    <p class="details">Saturday 30th April, 2022<br>10:00 am – 12:00 pm<br>42 Harlow Lane, Fernwood</p>

    <div class="feature-photo" role="img" aria-label="Photograph of a glowing plasma globe exhibit inside the STEM hub, lit in violet tones"></div>

    <div class="notes">
      <p>Light canapes provided. Dress code is smart/casual<br>All guests will be given a guided walk through of Australia’s first<br>dedicated STEM education hub for children aged 3-6.</p>
      <span class="invite-only">INVITATION ONLY</span>
    </div>

    <div class="pattern-band pattern-band--bottom" role="img" aria-label="Subtle tonal triangle pattern"></div>

    <div class="brand-bloom">
      <span class="brand-bloom__square"></span>
      <span class="brand-bloom__name">Bloom and Grow</span>
    </div>

    <p class="rsvp">RSVP: 18 April to marketing@bloomandgrow.edu.au</p>
  </article>
</body>
</html>
```